Stylish Business Cards Wanted

- DOUBLE SIDED Design Required -

High end, edgy cards for a corporate and personal stylist. Must include logo,
Name: Belinda Harwick
Title: Director and Stylist
telephone : +61 8 7142 5809
email: belinda@theloombriefing.example
website: theloombriefing.example
Tag: Corporate Workwear & Uniform Specialist | Personal Stylist
Would like nice icons for telephone, email, website

Target Market(s)

Businesses wanting stylish uniforms, people wanting stylish wardrobes

Industry/Entity Type

Corporate Workwear Stylist

Contact Information for Business Card

I would like black, white and gold foiling incorporated in the design - possibly a touch of the other colours on my branding guide attached Name: Belinda Harwick Title: Director and Stylist telephone : +61 8 7142 5809 email: belinda@theloombriefing.example website: theloombriefing.example Tag: Corporate Workwear & Uniform Specialist | Personal Stylist Would like nice icons for telephone, email, website

Font styles to use
Other font styles liked:
• Raleway

Colors

Designer to choose colors to be used in the design.

Requirements
Must have
• Gold foil accents

```html
<!DOCTYPE html>
<html lang="en">
<head>
<meta charset="utf-8">
<title>The Loom Briefing — Business Cards</title>
<link rel="stylesheet" href="https://fonts.googleapis.com/css2?family=Montserrat:wght@400;500&display=swap">
<style>
  :root {
    --backdrop: #2a2a2b;
    --card: #1c1c1d;
    --card-edge: #111112;
    --gold: #d4ad45;
    --text-light: #d9d9d9;
    --deco-tone: #232324;
  }
  * { box-sizing: border-box; margin: 0; padding: 0; }
  html, body { width: 1200px; height: 868px; overflow: hidden; }
  body {
    background: var(--backdrop);
    font-family: "Montserrat", Arial, sans-serif;
    position: relative;
  }
  .card {
    position: absolute;
    background: var(--card);
    box-shadow: 0 0 0 1px var(--card-edge), 0 18px 40px rgba(0,0,0,0.45);
  }
  .card-back {
    left: 110px; top: 164px; width: 330px; height: 540px;
    display: flex; flex-direction: column; align-items: center;
    text-align: center; overflow: hidden;
  }
  .monogram-watermark {
    position: absolute; left: 0; top: 40px; width: 100%; height: 460px;
    background: radial-gradient(ellipse at 50% 50%, var(--deco-tone) 0%, var(--card) 70%);
  }
  .back-content {
    position: relative; margin-top: 170px;
    display: flex; flex-direction: column; align-items: center;
  }
  .person-name {
    color: var(--gold); font-weight: 500; font-size: 19px;
    letter-spacing: 0.5px; text-transform: uppercase;
  }
  .person-title { color: var(--text-light); font-size: 11px; margin-top: 4px; }
  .gold-rule { width: 26px; height: 2px; background: var(--gold); margin: 18px 0; }
  .contact-line { color: var(--text-light); font-size: 10.5px; line-height: 1.55; }
  .service-line {
    color: var(--text-light); font-size: 10.5px; line-height: 1.5;
    text-transform: uppercase; letter-spacing: 0.4px;
  }
  .card-front {
    left: 550px; top: 269px; width: 540px; height: 330px;
    display: flex; align-items: center; justify-content: center;
  }
  .brand-name {
    color: var(--gold); font-weight: 500; font-size: 26px;
    letter-spacing: 5px; text-transform: uppercase;
  }
</style>
</head>
<body>
  <section class="card card-back">
    <div class="monogram-watermark" role="img" aria-label="Faint tonal brand decoration area"></div>
    <div class="back-content">
      <h1 class="person-name">Belinda Harwick</h1>
      <p class="person-title">Director &amp; Stylist</p>
      <div class="gold-rule"></div>
      <p class="contact-line">+61 8 7142 5809</p>
      <p class="contact-line">belinda@theloombriefing.example</p>
      <p class="contact-line">theloombriefing.example</p>
      <div class="gold-rule"></div>
      <p class="service-line">Corporate Workwear</p>
      <p class="service-line">Uniform Specialist</p>
      <p class="service-line">Personal Stylist</p>
    </div>
  </section>

  <section class="card card-front">
    <p class="brand-name">The Loom Briefing</p>
  </section>
</body>
</html>
```